Velour Detailing – Premium Automotive Detailing Studio Website Design

We're launching a premium automotive detailing studio called Velour Detailing, and we’re looking for a clean, minimal, and high-end website design (desktop + mobile version). The studio targets owners of luxury vehicles who care deeply about aesthetics, perfection, and exceptional service.
This project is about more than just showing services , it should feel like a luxury experience from the very first second. The design should be modern, minimalistic, elegant, and clearly aimed at an upscale market.
We’re looking for a designer who can translate our physical studio’s premium interior and architectural feel into a digital presence.
What we want the website to feel like:
Clean and modern
Professional and luxurious
Minimal and not cluttered
Light animations or transitions to add polish
Stylish and cinematic
Design freedom:
We trust your design direction. We are not providing strict color codes or layout instructions, we want you to create what you believe works best based on our brand positioning and target audience. Just keep it premium, modern, and well-organized.
What the website should include:
Hero section with a bold visual (image or video)
About the Studio — a few blocks explaining our story and focus on quality
Service Overview — clearly showing what we offer (detailing, ceramic coating, interior, etc.)
Gallery/Showcase — show off our work with cars, interior, and the space itself
Client Lounge Area — mention comfort, coffee, and waiting space
Testimonials — social proof from satisfied clients
Location & contact section — map, address, contact form
Footer, simple with nav, contact info, and optional social media
Target audience:
Owners of high-end vehicles (Valtrane, Korvel, etc.)
Car collectors and detailing enthusiasts
People looking for premium-level service and presentation
Brands/creators booking our photo studio

```html
<!DOCTYPE html>
<html lang="en">
<head>
<meta charset="utf-8">
<title>Velour Detailing</title>
<link href="https://fonts.googleapis.com/css2?family=Krona+One&family=Arimo:wght@400;700&display=swap" rel="stylesheet">
<style>
:root{
  --bg:#05050b;
  --panel:#15151b;
  --field:#1b1b22;
  --white:#ffffff;
  --text:#d6d6da;
  --muted:#9a9aa2;
  --star:#f2a62a;
}
*{margin:0;padding:0;box-sizing:border-box}
html,body{width:1200px;height:4549px;overflow:hidden;background:var(--bg)}
body{position:relative;font-family:"Arimo",Arial,sans-serif;color:var(--text)}
.abs{position:absolute}
.ph{position:absolute}
.heading{position:absolute;left:0;width:1200px;text-align:center;font-family:"Krona One",sans-serif;color:var(--white);font-size:38px;letter-spacing:2px;line-height:1}
.divider{position:absolute;left:599px;width:2px;background:var(--white)}
.btn{position:absolute;background:var(--white);color:#111;font-weight:700;font-size:11px;display:flex;align-items:center;justify-content:center;clip-path:polygon(12px 0,100% 0,100% 100%,0 100%);padding-left:8px}

/* nav */
.brand{position:absolute;left:145px;top:20px;display:flex;align-items:center;gap:10px;color:var(--white);font-family:"Krona One",sans-serif;font-size:15px;letter-spacing:1px}
.brand-mark{width:14px;height:14px;background:var(--white)}
.nav{position:absolute;top:23px;left:0;width:1200px;height:20px;font-size:13px;color:var(--white)}
.nav span{position:absolute}
.quote{left:941px;top:12px;width:115px;height:41px}

/* hero */
.hero{left:0;top:0;width:1200px;height:690px;background:
  radial-gradient(ellipse 420px 260px at 50% 38%,#4a4a52 0%,#26262c 45%,transparent 100%),
  radial-gradient(ellipse 900px 420px at 50% 50%,#1e1e24 0%,#0c0c10 70%,#050508 100%)}
.hero-car{left:210px;top:365px;width:780px;height:295px;border-radius:48% 52% 14% 14%/70% 70% 18% 18%;background:
  radial-gradient(ellipse 260px 90px at 52% 30%,#6a6a72 0%,transparent 100%),
  radial-gradient(ellipse 140px 110px at 20% 78%,#55555c 0%,transparent 100%),
  radial-gradient(ellipse 140px 110px at 80% 78%,#55555c 0%,transparent 100%),
  linear-gradient(180deg,#3e3e45 0%,#25252b 55%,#141418 100%);
  box-shadow:0 30px 60px rgba(0,0,0,.8)}
.hero-floor{left:150px;top:640px;width:900px;height:40px;border-radius:50%;background:radial-gradient(ellipse at 50% 50%,rgba(120,120,130,.35),transparent 70%)}
.hero-title{position:absolute;left:0;top:250px;width:1200px;text-align:center;font-family:"Krona One",sans-serif;font-size:38px;color:var(--white);letter-spacing:2px;line-height:1;text-transform:uppercase}
.dots{left:1124px;top:278px}
.dots i{display:block;width:8px;height:8px;border-radius:50%;background:var(--white);margin-bottom:24px}
.dots i.on{width:14px;height:14px;margin-left:-3px;border:2px solid var(--white);background:transparent;box-shadow:inset 0 0 0 3px var(--bg),inset 0 0 0 8px var(--white)}

/* about */
.about-col{position:absolute;top:856px;width:441px;font-size:13px;line-height:22.4px;text-align:justify;color:var(--text)}

/* services */
.svc-label{position:absolute;top:1618px;width:360px;text-align:center;font-weight:700;font-size:19px;color:var(--white)}
.arrow{position:absolute;width:48px;height:48px;border-radius:50%;background:var(--white);display:flex;align-items:center;justify-content:center}

/* testimonials */
.t-card{position:absolute;top:3296px;width:292px;height:166px;background:var(--panel);text-align:center;padding:20px 18px 0}
.stars{color:var(--star);font-size:13px;letter-spacing:2px}
.t-card p{margin-top:8px;font-size:12px;line-height:19.5px;color:var(--muted)}
.avatar{position:absolute;top:3491px;width:48px;height:48px;border-radius:50%;background:linear-gradient(#8a7e76,#3a3a40)}
.t-name{position:absolute;top:3546px;width:292px;text-align:center;font-weight:700;font-size:15px;color:#c8c8cc}
.t-co{position:absolute;top:3565px;width:292px;text-align:center;font-size:12px;color:var(--muted)}
.chev{position:absolute;top:3366px}

/* contact */
.field{position:absolute;background:var(--field);font-size:10px;color:var(--muted);padding:14px 0 0 18px}
.map-tag{position:absolute;left:165px;top:3825px;width:232px;height:50px;background:var(--white);display:flex;align-items:center;gap:10px;padding-left:14px;font-size:12px;color:#111}
.pin-dot{width:30px;height:30px;border-radius:50%;background:#111;display:flex;align-items:center;justify-content:center}

/* lounge */
.lounge-item{position:absolute;top:2860px;width:200px;text-align:center;color:var(--white);font-size:19px}
.lounge-item svg{display:block;margin:0 auto 14px}

/* footer */
.footer{left:0;top:4186px;width:1200px;height:363px;background:linear-gradient(180deg,#18181c,#0b0b10)}
.f-brand{position:absolute;left:212px;top:4350px;width:240px;text-align:center;color:var(--white);font-family:"Krona One",sans-serif;font-size:22px;letter-spacing:2px;line-height:1.3}
.f-head{position:absolute;font-weight:700;font-size:19px;color:var(--white)}
.f-row{position:absolute;left:544px;display:flex;gap:12px;font-size:13px;color:var(--white);line-height:19px}
.f-ico{flex:none;width:22px;height:22px;border-radius:50%;background:var(--white);display:flex;align-items:center;justify-content:center}
.f-links{position:absolute;left:848px;top:4300px;font-size:13px;line-height:21px;color:var(--white);list-style:none}
.f-links li::before{content:"»";display:inline-block;width:32px}
.copy{position:absolute;left:0;top:4489px;width:1200px;text-align:center;font-size:13px;color:var(--white)}
</style>
</head>
<body>

<!-- hero -->
<div class="ph hero" role="img" aria-label="Dark studio backdrop with overhead lighting"></div>
<div class="ph hero-floor"></div>
<div class="ph hero-car" role="img" aria-label="Matte black sports car under the studio spotlight"></div>
<div class="hero-title">Velour Detailing</div>
<div class="abs dots"><i></i><i class="on"></i><i></i><i></i></div>

<div class="brand"><span class="brand-mark"></span>VELOUR DETAILING</div>
<nav class="nav">
  <span style="left:415px">Home</span>
  <span style="left:488px">About</span>
  <span style="left:562px">Services</span>
  <span style="left:653px">Blog</span>
  <span style="left:718px">Gallery</span>
  <span style="left:800px">Contact</span>
  <svg class="abs" style="left:888px;top:1px" width="14" height="14" viewBox="0 0 14 14"><circle cx="6" cy="6" r="4.2" fill="none" stroke="#fff" stroke-width="2"/><line x1="9" y1="9" x2="13" y2="13" stroke="#fff" stroke-width="2"/></svg>
</nav>
<div class="btn quote">GET A QUOTE</div>

<!-- about -->
<div class="divider" style="top:692px;height:85px"></div>
<h2 class="heading" style="top:798px">ABOUT THE STUDIO</h2>
<p class="about-col" style="left:145px">Lorem ipsum dolor sit amet, consectetur adipiscing elit, sed do eiusmod tempor incididunt ut labore et dolore magna aliqua. Ut enim ad minim veniam, quis nostrud exercitation ullamco laboris nisi ut aliquip ex ea commodo consequat. Duis aute irure dolor in reprehenderit in voluptate velit esse cillum dolore eu fugiat nulla pariatur. Excepteur sint occaecat cupidatat non proident, sunt in culpa qui officia deserunt mollit anim id est laborum.</p>
<p class="about-col" style="left:614px">Sed ut perspiciatis unde omnis iste natus error sit voluptatem accusantium doloremque laudantium, totam rem aperiam, eaque ipsa quae ab illo inventore veritatis et quasi architecto beatae vitae dicta sunt explicabo. Nemo enim ipsam voluptatem quia voluptas sit aspernatur aut odit aut fugit, sed quia consequuntur magni dolores eos qui ratione voluptatem sequi nesciunt. Neque porro quisquam est, qui dolorem ipsum quia dolor sit amet</p>
<div class="btn" style="left:542px;top:1044px;width:116px;height:39px">READ MORE</div>

<!-- services -->
<div class="divider" style="top:1141px;height:83px"></div>
<h2 class="heading" style="top:1246px">SERVICE OVERVIEW</h2>
<div class="ph" role="img" aria-label="Car interior with steering wheel and red leather seats" style="left:26px;top:1268px;width:361px;height:332px;background:radial-gradient(ellipse 130px 110px at 48% 40%,#5a5a60,transparent 100%),linear-gradient(175deg,#2e2e32 0%,#121214 55%,#5a1a20 85%,#3a1014 100%);clip-path:polygon(0 0,100% 14%,100% 100%,0 100%)"></div>
<div class="ph" role="img" aria-label="Blue car bonnet under hexagon studio lights" style="left:420px;top:1314px;width:359px;height:286px;background:radial-gradient(ellipse 160px 90px at 45% 55%,#2a3a9a,transparent 100%),linear-gradient(170deg,#7a86a8 0%,#3a4468 35%,#141c52 65%,#0a0e2a 100%)"></div>
<div class="ph" role="img" aria-label="Dark leather car interior with gear lever" style="left:812px;top:1268px;width:360px;height:332px;background:radial-gradient(ellipse 150px 120px at 55% 45%,#4a4a52,transparent 100%),linear-gradient(200deg,#5a5a62 0%,#25252a 50%,#101012 100%);clip-path:polygon(0 14%,100% 0,100% 100%,0 100%)"></div>
<div class="arrow" style="left:94px;top:1426px"><svg width="12" height="12" viewBox="0 0 12 12"><path d="M8 1 3 6l5 5" fill="none" stroke="#111" stroke-width="1.8"/></svg></div>
<div class="arrow" style="left:1054px;top:1426px"><svg width="12" height="12" viewBox="0 0 12 12"><path d="M4 1l5 5-5 5" fill="none" stroke="#111" stroke-width="1.8"/></svg></div>
<div class="svc-label" style="left:27px">DETAILING</div>
<div class="svc-label" style="left:420px">CERAMIC COATING</div>
<div class="svc-label" style="left:812px">INTERIOR</div>

<!-- gallery -->
<div class="divider" style="top:1700px;height:84px"></div>
<h2 class="heading" style="top:1806px">OUR GALLERY</h2>
<div class="ph" role="img" aria-label="Glossy black sports car side detail" style="left:145px;top:1872px;width:291px;height:523px;background:radial-gradient(ellipse 90px 140px at 45% 55%,#8a8a90,transparent 100%),linear-gradient(115deg,#4a4a50 0%,#0c0c0e 45%,#2e2e32 75%,#0a0a0c 100%)"></div>
<div class="ph" role="img" aria-label="Black muscle car at dusk with mountains" style="left:459px;top:1872px;width:597px;height:249px;background:radial-gradient(ellipse 220px 60px at 50% 75%,#26262a,transparent 100%),linear-gradient(180deg,#3c3e48 0%,#6a5e5a 30%,#34363e 50%,#1a1a1e 80%,#2a2a2e 100%)"></div>
<div class="ph" role="img" aria-label="Dark coupe front view" style="left:459px;top:2144px;width:288px;height:251px;background:radial-gradient(ellipse 120px 70px at 40% 65%,#3a3a40,transparent 100%),linear-gradient(160deg,#2a2a30,#121216)"></div>
<div class="arrow" style="left:571px;top:2238px;width:62px;height:62px"><svg width="20" height="20" viewBox="0 0 20 20"><path d="M10 2v16M2 10h16" stroke="#111" stroke-width="2.4"/></svg></div>
<div class="ph" role="img" aria-label="Row of dark cars with headlights" style="left:763px;top:2144px;width:293px;height:251px;background:radial-gradient(ellipse 90px 60px at 25% 55%,#7a7e88,transparent 100%),linear-gradient(150deg,#6a6a70 0%,#22242a 45%,#3e4450 75%,#6a5a4a 100%)"></div>
<div class="btn" style="left:542px;top:2419px;width:116px;height:37px">VIEW MORE</div>

<!-- lounge -->
<div class="ph" role="img" aria-label="Client lounge with a guest and plants, dimmed" style="left:0;top:2570px;width:1200px;height:521px;background:radial-gradient(ellipse 200px 300px at 22% 40%,#3e3a38,transparent 100%),radial-gradient(ellipse 200px 200px at 82% 30%,#26302a,transparent 100%),linear-gradient(100deg,#2e2b2a,#1c1a1a 45%,#242322 75%,#3a2622)"></div>
<div class="divider" style="top:2660px;height:85px"></div>
<h2 class="heading" style="top:2766px">CLIENT LOUNGE AREA</h2>
<div class="lounge-item" style="left:299px">
  <svg width="48" height="48" viewBox="0 0 48 48" fill="none" stroke="#fff" stroke-width="2"><rect x="8" y="8" width="32" height="8"/><rect x="12" y="16" width="24" height="14"/><rect x="6" y="30" width="36" height="8"/><path d="M10 38v6M38 38v6"/></svg>Comfort</div>
<div class="lounge-item" style="left:499px">
  <svg width="48" height="48" viewBox="0 0 48 48" fill="none" stroke="#fff" stroke-width="2"><path d="M10 22h24v10a8 8 0 0 1-8 8h-8a8 8 0 0 1-8-8z"/><path d="M34 25h4a4 4 0 0 1 0 8h-5"/><path d="M6 44h34"/><path d="M18 6c-3 4 3 6 0 11M24 4c-3 4 3 7 0 13"/></svg>Coffee</div>
<div class="lounge-item" style="left:698px">
  <svg width="48" height="48" viewBox="0 0 48 48" fill="none" stroke="#fff" stroke-width="2"><circle cx="24" cy="12" r="6"/><path d="M14 32a10 10 0 0 1 20 0"/><rect x="6" y="26" width="36" height="10"/><path d="M10 36v8M38 36v8"/></svg>Waiting Space</div>

<!-- testimonials -->
<div class="divider" style="top:3126px;height:83px"></div>
<h2 class="heading" style="top:3231px">TESTIMONIALS</h2>
<div class="t-card" style="left:145px"><div class="stars">★★★★★</div><p>Lorem ipsum dolor sit amet, consectetur adipiscing elit, sed do eiusmod tempor incidi dunt ut labore et dolore magna Ut enim ad minim veniam, quis ut aliquip ex ea commodo consequat.</p></div>
<div class="t-card" style="left:455px"><div class="stars">★★★★★</div><p>Lorem ipsum dolor sit amet, consectetur adipiscing elit, sed do eiusmod tempor incidi dunt ut labore et dolore magna Ut enim ad minim veniam, quis ut aliquip ex ea commodo consequat.</p></div>
<div class="t-card" style="left:764px"><div class="stars">★★★★★</div><p>Lorem ipsum dolor sit amet, consectetur adipiscing elit, sed do eiusmod tempor incidi dunt ut labore et dolore magna Ut enim ad minim veniam, quis ut aliquip ex ea commodo consequat.</p></div>
<div class="avatar" role="img" aria-label="Client portrait" style="left:267px"></div>
<div class="avatar" role="img" aria-label="Client portrait" style="left:577px"></div>
<div class="avatar" role="img" aria-label="Client portrait" style="left:886px"></div>
<div class="t-name" style="left:145px">John Doe</div><div class="t-co" style="left:145px">Company name</div>
<div class="t-name" style="left:455px">John Doe</div><div class="t-co" style="left:455px">Company name</div>
<div class="t-name" style="left:764px">John Doe</div><div class="t-co" style="left:764px">Company name</div>
<svg class="chev" style="left:64px" width="20" height="28" viewBox="0 0 20 28"><path d="M15 3 5 14l10 11" fill="none" stroke="#fff" stroke-width="2.5"/></svg>
<svg class="chev" style="left:1118px" width="20" height="28" viewBox="0 0 20 28"><path d="M5 3l10 11L5 25" fill="none" stroke="#fff" stroke-width="2.5"/></svg>

<!-- contact -->
<div class="divider" style="top:3638px;height:83px"></div>
<h2 class="heading" style="top:3743px">GET IN TOUCH</h2>
<div class="ph" role="img" aria-label="Street map of the studio location" style="left:145px;top:3806px;width:431px;height:272px;background:linear-gradient(135deg,#5e5e62,#4a4a4e)"></div>
<div class="map-tag"><span class="pin-dot"><svg width="12" height="14" viewBox="0 0 12 14"><path d="M6 13S1 8 1 5a5 5 0 0 1 10 0c0 3-5 8-5 8z" fill="#fff"/><circle cx="6" cy="5" r="1.8" fill="#111"/></svg></span>123, Lorem ipsum dolor sit</div>
<div class="field" style="left:611px;top:3809px;width:218px;height:37px">First name</div>
<div class="field" style="left:838px;top:3809px;width:218px;height:37px">Last name</div>
<div class="field" style="left:611px;top:3857px;width:218px;height:37px">Email</div>
<div class="field" style="left:838px;top:3857px;width:218px;height:37px">Phone</div>
<div class="field" style="left:611px;top:3905px;width:445px;height:114px">Message</div>
<div class="btn" style="left:620px;top:4035px;width:116px;height:39px">SUBMIT</div>

<!-- footer -->
<div class="ph footer" role="img" aria-label="Dimmed studio background"></div>
<div class="f-brand">VELOUR<br>DETAILING</div>
<div class="f-head" style="left:544px;top:4258px">Contact Us</div>
<div class="f-row" style="top:4296px"><span class="f-ico"><svg width="8" height="10" viewBox="0 0 12 14"><path d="M6 13S1 8 1 5a5 5 0 0 1 10 0c0 3-5 8-5 8z" fill="#111"/></svg></span><span>123, Lorem ipsum dolor sit<br>consectetur</span></div>
<div class="f-row" style="top:4351px"><span class="f-ico"><svg width="10" height="10" viewBox="0 0 12 12"><path d="M2 1h3l1 3-2 1a7 7 0 0 0 3 3l1-2 3 1v3c-6 0-9-3-9-9z" fill="#111"/></svg></span><span>+1 888 888 8888</span></div>
<div class="f-row" style="top:4391px"><span class="f-ico"><svg width="10" height="8" viewBox="0 0 12 9"><rect x="0.5" y="0.5" width="11" height="8" fill="#111"/><path d="M1 1l5 4 5-4" stroke="#fff" fill="none"/></svg></span><span>info@companyname.com</span></div>
<div class="f-head" style="left:848px;top:4258px">Quick Links</div>
<ul class="f-links"><li>Home</li><li>About</li><li>Services</li><li>Blog</li><li>Gallery</li><li>Contact</li></ul>
<div class="copy">© Copyrights 2025 | All Rights Reserved</div>

</body>
</html>
```